TREVAL BUILDWORKS, LLC Webpage portfolio

I want to create a Website that allows my potential clients to browse my Skilled work via before and after photos. I want the website to enhance the work that I provide and potentially drive new business, or at least solidify my work.
I also do 3D CAD and Modeling of New Spaces and it would be nice to show some of that work from pencil design to 3D modeling, which I feel may help give me more clients.

The website needs to show a solid carpenter/company with the skills to get any project completed.

Types of Jobs - Custom Carpentry & Finishes, Kitchens, Baths, Basements, Decks, Porches, Whole House Renovation - Skilled Craftsmanship (Hardwood Flooring, Floor and Wall Tile) and much more...

Target Market(s)

Residential Home Renovation, Kitchen and Bath Renovation, Home Improvement

Industry/Entity Type

Residential Construction

Number of Pages Required

5+ page

Font styles to use
Sans Serif
Script

Requirements
Must have
• Similar to Plinvo.com, except for Treval Buildworks.
• Must be inviting.
• My Services Offered
• A way to reach me or contact me for estimates with some sort of Screening Questionare.
Nice to have
• Inviting Colors
Should not have
• Not sure at this time

```html
<!DOCTYPE html>
<html lang="en">
<head>
<meta charset="utf-8">
<title>Treval Buildworks – Design, Build &amp; Remodeling Contractors</title>
<link href="https://fonts.googleapis.com/css2?family=Questrial&family=Open+Sans:wght@400;600&display=swap" rel="stylesheet">
<style>
:root{
  --navy:#1d3e5c;
  --blue:#2a9fd6;
  --social:#1f5c94;
  --text:#333a40;
  --muted:#8a9096;
  --line:#e3e3e3;
  --band:#f2f2f2;
  --white:#ffffff;
}
*{box-sizing:border-box;margin:0;padding:0}
html,body{width:1200px;height:3346px;overflow:hidden;background:var(--white)}
body{position:relative;font-family:'Open Sans',Arial,sans-serif;color:var(--text)}
h1,h2,h3{font-weight:400}
.heading{font-family:'Questrial',Arial,sans-serif;color:var(--navy)}

/* header */
.site-header{position:absolute;left:0;top:0;width:1200px;height:161px;background:var(--white)}
.brand{position:absolute;left:134px;top:38px;display:flex;flex-direction:column;align-items:flex-start}
.brand-mark{width:40px;height:40px;background:var(--navy);margin-left:10px}
.brand-name{font-family:'Questrial',Arial,sans-serif;font-size:28px;color:var(--navy);line-height:1;margin-top:8px}
.brand-tag{font-size:9.5px;letter-spacing:1.1px;color:var(--blue);font-weight:600;margin-top:6px}
.search{position:absolute;left:785px;top:33px;width:178px;height:34px;border:1px solid #d5d5d5;border-radius:3px;font-size:12px;color:#666;padding:9px 12px}
.search svg{position:absolute;right:11px;top:10px}
.btn-signin{position:absolute;left:977px;top:33px;width:89px;height:34px;background:var(--blue);color:var(--white);border-radius:3px;font-size:11px;display:flex;align-items:center;justify-content:center;gap:6px}
.main-nav{position:absolute;top:117px;right:134px;display:flex;gap:34px;font-size:12px;letter-spacing:.4px;color:#222}
.main-nav .active{text-decoration:underline;text-underline-offset:5px;color:var(--navy)}

/* hero */
.hero{position:absolute;left:0;top:161px;width:1200px;height:452px;
  background:radial-gradient(ellipse at 50% 45%,rgba(120,95,75,.55) 0%,rgba(0,0,0,0) 60%),
             linear-gradient(180deg,#3f2e22 0%,#5e4331 40%,#4a3a30 70%,#231c18 100%)}
.hero-title{position:absolute;left:0;top:150px;width:1200px;text-align:center;font-family:'Questrial',Arial,sans-serif;font-size:31px;line-height:44px;color:var(--white)}
.btn-register{position:absolute;left:528px;top:252px;width:143px;height:36px;background:var(--blue);color:var(--white);font-size:11px;border-radius:2px;display:flex;align-items:center;justify-content:center;gap:6px}
.hero-arrow{position:absolute;top:212px;width:26px;height:26px;border-radius:50%;background:rgba(255,255,255,.5);display:flex;align-items:center;justify-content:center}

/* intro features */
.section-title{position:absolute;left:0;width:1200px;text-align:center;font-size:30px}
.feature{position:absolute;width:300px;text-align:center}
.feature svg{display:block;margin:0 auto}
.feature-title{font-family:'Questrial',Arial,sans-serif;font-size:20px;color:var(--navy);margin-top:18px}
.feature-text{font-size:10px;line-height:14px;color:var(--muted);margin-top:6px}

/* jobs */
.jobs-band{position:absolute;left:0;top:988px;width:1200px;height:1280px;background:var(--band)}
.job-card{position:absolute;width:296px;height:326px;background:var(--white)}
.job-photo{height:199px}
.job-title{font-family:'Questrial',Arial,sans-serif;font-size:15px;color:#222;text-align:center;margin-top:28px}
.job-text{font-size:9.5px;line-height:14px;color:var(--muted);text-align:center;padding:6px 26px 0}

/* portfolio */
.portfolio-item{position:absolute;top:2402px;width:296px}
.portfolio-photo{height:192px;display:flex;position:relative}
.portfolio-photo .half{flex:1}
.tag{position:absolute;top:0;background:#2a2a2a;color:var(--white);font-size:8px;padding:5px 10px;letter-spacing:.5px}
.portfolio-caption{font-family:'Questrial',Arial,sans-serif;font-size:16px;color:#222;text-align:center;margin-top:12px}
.btn-view{position:absolute;left:560px;top:2658px;width:80px;height:36px;border:1px solid #cfcfcf;font-size:10px;display:flex;align-items:center;justify-content:center;color:#333}

/* testimonial */
.testimonial{position:absolute;left:134px;top:2774px;width:932px;height:319px;
  background:linear-gradient(180deg,#3e342e 0%,#5a5048 35%,#6a5e54 60%,#2f2924 100%)}
.quote{position:absolute;left:76px;top:78px;width:780px;text-align:center;font-family:'Questrial',Arial,sans-serif;font-size:16px;line-height:27px;color:var(--white)}
.quote-author{display:block;margin-top:6px}
.dots{position:absolute;top:232px;left:0;width:932px;display:flex;justify-content:center;gap:14px}
.dots span{width:7px;height:7px;border-radius:50%;background:rgba(255,255,255,.5)}
.dots span.on{background:var(--white)}

/* contact + footer */
.contact-row{position:absolute;top:3146px;left:0;width:1200px;font-size:14px;color:#222}
.contact-row div{position:absolute;display:flex;align-items:center;gap:7px}
.footer-rule{position:absolute;left:0;top:3214px;width:1200px;height:1px;background:var(--line)}
.footer-links{position:absolute;left:134px;top:3258px;font-size:10.5px;color:#444}
.footer-links span{margin:0 8px;color:#999}
.copyright{position:absolute;left:134px;top:3285px;font-size:10.5px;color:#555}
.social{position:absolute;left:977px;top:3264px;display:flex;gap:7px}
.social span{width:26px;height:26px;border-radius:50%;background:var(--social)}
</style>
</head>
<body>

<header class="site-header">
  <div class="brand"><span class="brand-mark"></span><span class="brand-name">Treval Buildworks</span><span class="brand-tag">DESIGN, BUILD &amp; REMODELING CONTRACTORS</span></div>
  <div class="search">Search
    <svg width="12" height="12" viewBox="0 0 12 12"><circle cx="5" cy="5" r="3.6" fill="none" stroke="#555" stroke-width="1.4"/><line x1="7.6" y1="7.6" x2="11" y2="11" stroke="#555" stroke-width="1.4"/></svg>
  </div>
  <div class="btn-signin">
    <svg width="9" height="11" viewBox="0 0 9 11"><rect x="0" y="5" width="9" height="6" fill="#fff"/><path d="M2 5V3.2a2.5 2.5 0 0 1 5 0V5" fill="none" stroke="#fff" stroke-width="1.3"/></svg>SIGN IN
  </div>
  <nav class="main-nav"><span class="active">HOME</span><span>ABOUT US</span><span>SERVICES</span><span>PORTFOLIO</span><span>CONTACT US</span></nav>
</header>

<section class="hero" role="img" aria-label="Photo of a renovated living room with a stone fireplace and built-in wooden shelving">
  <h1 class="hero-title">Phasellus rhoncus lectus eu magna pulvinar<br>in lobortis magna dignissim</h1>
  <div class="btn-register">
    <svg width="10" height="10" viewBox="0 0 10 10"><path d="M1 9l.6-2.4L7 1.2 8.8 3 3.4 8.4z" fill="#fff"/></svg>REGISTER NOW
  </div>
  <div class="hero-arrow" style="left:24px"><svg width="8" height="10" viewBox="0 0 8 10"><path d="M6 1L2 5l4 4" fill="none" stroke="#444" stroke-width="1.8"/></svg></div>
  <div class="hero-arrow" style="left:1150px"><svg width="8" height="10" viewBox="0 0 8 10"><path d="M2 1l4 4-4 4" fill="none" stroke="#444" stroke-width="1.8"/></svg></div>
</section>

<h2 class="heading section-title" style="top:676px">Fusce congue volutpat orci quis iaculis</h2>

<div class="feature" style="left:118px;top:758px">
  <svg width="44" height="52" viewBox="0 0 44 52" fill="none" stroke="#1d3e5c" stroke-width="2"><path d="M14 32c-5-4-8-9-8-15a16 16 0 0 1 32 0c0 6-3 11-8 15v6H14z"/><line x1="15" y1="43" x2="29" y2="43"/><line x1="17" y1="48" x2="27" y2="48"/></svg>
  <div class="feature-title">Ideas for Interiors</div>
  <p class="feature-text">Praesent risus leo, fringilla vel tincidunt nec, molestie non lectus. Cum sociis natoque penatibus et magnis dis parturient montes, nascetur ridiculus mus.</p>
</div>
<div class="feature" style="left:448px;top:758px">
  <svg width="52" height="52" viewBox="0 0 52 52" fill="none" stroke="#1d3e5c" stroke-width="2"><path d="M8 40L38 10l6 6-30 30-8 2z"/><line x1="33" y1="15" x2="39" y2="21"/><rect x="6" y="6" width="12" height="40" transform="rotate(-45 26 26)"/></svg>
  <div class="feature-title">Quisque bibendum</div>
  <p class="feature-text">Praesent risus leo, fringilla vel tincidunt nec, molestie non lectus. Cum sociis natoque penatibus et magnis dis parturient montes, nascetur ridiculus mus.</p>
</div>
<div class="feature" style="left:771px;top:758px">
  <svg width="60" height="52" viewBox="0 0 60 52" fill="none" stroke="#1d3e5c" stroke-width="2"><rect x="3" y="6" width="54" height="34"/><rect x="8" y="11" width="44" height="24"/><line x1="30" y1="40" x2="30" y2="47"/><line x1="18" y1="48" x2="42" y2="48"/></svg>
  <div class="feature-title">Donec ultrices dolor</div>
  <p class="feature-text">Praesent risus leo, fringilla vel tincidunt nec, molestie non lectus. Cum sociis natoque penatibus et magnis dis parturient montes, nascetur ridiculus mus.</p>
</div>

<div class="jobs-band"></div>
<h2 class="heading section-title" style="top:1062px">Types of Jobs</h2>

<article class="job-card" style="left:134px;top:1137px">
  <div class="job-photo" role="img" aria-label="Photo of custom wood cabinetry and finishes" style="background:linear-gradient(180deg,#4a3322 0%,#7a5232 45%,#3a2416 100%)"></div>
  <h3 class="job-title">Custom Carpentry &amp; Finishes</h3>
  <p class="job-text">Praesent risus leo, fringilla vel tincidunt nec, molestie non lectus. Cum sociis natoque penatibus et magnis dis parturient montes, nascetur ridiculus mus.</p>
</article>
<article class="job-card" style="left:452px;top:1137px">
  <div class="job-photo" role="img" aria-label="Photo of a kitchen with granite island" style="background:linear-gradient(180deg,#5a4030 0%,#8c6a4e 50%,#b0957a 70%,#4a3526 100%)"></div>
  <h3 class="job-title">Kitchens</h3>
  <p class="job-text">Praesent risus leo, fringilla vel tincidunt nec, molestie non lectus. Cum sociis natoque penatibus et magnis dis parturient montes, nascetur ridiculus mus.</p>
</article>
<article class="job-card" style="left:770px;top:1137px">
  <div class="job-photo" role="img" aria-label="Photo of a bathroom vanity with vessel sink" style="background:linear-gradient(90deg,#b8a488 0%,#8a6a54 45%,#6a2a30 70%,#e8e2da 100%)"></div>
  <h3 class="job-title">Baths</h3>
  <p class="job-text">Praesent risus leo, fringilla vel tincidunt nec, molestie non lectus. Cum sociis natoque penatibus et magnis dis parturient montes, nascetur ridiculus mus.</p>
</article>

<article class="job-card" style="left:134px;top:1490px">
  <div class="job-photo" role="img" aria-label="Photo of a basement under framing" style="background:linear-gradient(180deg,#e4dccc 0%,#c2a47a 35%,#9c7e5a 75%,#6e5a44 100%)"></div>
  <h3 class="job-title">Basements</h3>
  <p class="job-text">Praesent risus leo, fringilla vel tincidunt nec, molestie non lectus. Cum sociis natoque penatibus et magnis dis parturient montes, nascetur ridiculus mus.</p>
</article>
<article class="job-card" style="left:452px;top:1490px">
  <div class="job-photo" role="img" aria-label="Photo of a stained wooden deck" style="background:linear-gradient(180deg,#8c6a50 0%,#6a4e3c 35%,#4a3428 70%,#2e201a 100%)"></div>
  <h3 class="job-title">Decks</h3>
  <p class="job-text">Praesent risus leo, fringilla vel tincidunt nec, molestie non lectus. Cum sociis natoque penatibus et magnis dis parturient montes, nascetur ridiculus mus.</p>
</article>
<article class="job-card" style="left:770px;top:1490px">
  <div class="job-photo" role="img" aria-label="Photo of a white porch with stairs" style="background:linear-gradient(180deg,#a8a49a 0%,#dcd8d0 45%,#b8b4a6 65%,#6e7a4e 100%)"></div>
  <h3 class="job-title">Porches</h3>
  <p class="job-text">Praesent risus leo, fringilla vel tincidunt nec, molestie non lectus. Cum sociis natoque penatibus et magnis dis parturient montes, nascetur ridiculus mus.</p>
</article>

<article class="job-card" style="left:452px;top:1840px">
  <div class="job-photo" role="img" aria-label="Photo of a room stripped for whole house renovation" style="background:linear-gradient(180deg,#b4a292 0%,#d8ccbc 40%,#8e7866 70%,#5e4c40 100%)"></div>
  <h3 class="job-title">Whole House Renovation</h3>
  <p class="job-text">Praesent risus leo, fringilla vel tincidunt nec, molestie non lectus. Cum sociis natoque penatibus et magnis dis parturient montes, nascetur ridiculus mus.</p>
</article>

<h2 class="heading section-title" style="top:2338px">Portfolio</h2>

<div class="portfolio-item" style="left:134px">
  <div class="portfolio-photo" role="img" aria-label="Before and after photos of a kitchen remodel">
    <div class="half" style="background:linear-gradient(180deg,#f0e6d2 0%,#d8c2a0 50%,#a08866 100%)"></div>
    <div class="half" style="background:linear-gradient(180deg,#a86a3a 0%,#7a4a2a 50%,#3e2616 100%)"></div>
    <span class="tag" style="left:0">BEFORE</span><span class="tag" style="left:148px">AFTER</span>
  </div>
  <div class="portfolio-caption">Phasellus rhoncus lectus</div>
</div>
<div class="portfolio-item" style="left:452px">
  <div class="portfolio-photo" role="img" aria-label="3D model rendering of a modern house" style="background:radial-gradient(ellipse at 50% 55%,#9aa0aa 0%,#dfe1e5 45%,#f6f6f6 100%)"></div>
  <div class="portfolio-caption">Phasellus rhoncus lectus</div>
</div>
<div class="portfolio-item" style="left:770px">
  <div class="portfolio-photo" role="img" aria-label="Before and after photos of a living area renovation">
    <div class="half" style="background:linear-gradient(180deg,#a89a8a 0%,#7a6656 50%,#3e322a 100%)"></div>
    <div class="half" style="background:linear-gradient(180deg,#e4dcc0 0%,#c8c4a0 50%,#7aa08a 100%)"></div>
    <span class="tag" style="left:0">BEFORE</span><span class="tag" style="left:148px">AFTER</span>
  </div>
  <div class="portfolio-caption">Phasellus rhoncus lectus</div>
</div>
<div class="btn-view">VIEW ALL</div>

<section class="testimonial" role="img" aria-label="Photo of a raised porch with white railings, behind a client quote">
  <blockquote class="quote">" Praesent vitae dolor sit amet lectus pretium aliquet quis a massa. Nulla felis libero, pellentesque lao-<br>reet tortor et, tincidunt auctor metus. Etiam vitae volutpat diam. Morbi dui augue, aliquam quis leo<br>blandit, cursus vehicula tortor. "<span class="quote-author">- Mara Lindell, City</span></blockquote>
  <div class="dots"><span class="on"></span><span></span><span></span><span></span></div>
</section>

<div class="contact-row">
  <div style="left:166px"><svg width="10" height="13" viewBox="0 0 10 13"><path d="M5 13S0 7.5 0 5a5 5 0 0 1 10 0c0 2.5-5 8-5 8z" fill="#333"/><circle cx="5" cy="5" r="1.8" fill="#fff"/></svg>24 Building name, Street name, City - Zipcode</div>
  <div style="left:622px"><svg width="9" height="13" viewBox="0 0 9 13"><rect x="0.5" y="0.5" width="8" height="12" rx="1.5" fill="#333"/><rect x="2" y="2" width="5" height="7" fill="#fff"/></svg>555 010 2468</div>
  <div style="left:810px"><svg width="13" height="10" viewBox="0 0 13 10"><rect width="13" height="10" fill="#333"/><path d="M0 0l6.5 5L13 0" fill="none" stroke="#fff" stroke-width="1.2"/></svg>info@trevalbuildworks.com</div>
</div>

<div class="footer-rule"></div>
<footer>
  <div class="footer-links">Home<span>|</span>About Us<span>|</span>Services<span>|</span>Portfolio<span>|</span>Contact Us</div>
  <div class="copyright">Copyright © 2017 Company name. All rights reserved.</div>
  <div class="social" aria-label="Social links"><span></span><span></span><span></span></div>
</footer>

</body>
</html>
```